Christmas Collection Candle Label Design

Looking to update our existing Christmas Candle Collection labels. Labels should reflect the overall feel of our brand- www.kelvanoro.ca
Want to include some color elements. Holiday colors added into design but more muted/ earthy tones not vibrant colors . Metallic elements and line art botanical illustration. Fonts should be more align to brand
Scents
Holiday Tree
Candy Cane
Sugar and Spice
Joyeaux Noel

```html
<!DOCTYPE html>
<html lang="en">
<head>
<meta charset="utf-8">
<title>Joyeaux Noel – Christmas Collection Candle Label</title>
<link rel="stylesheet" href="https://fonts.googleapis.com/css2?family=Tinos:wght@400;700&family=Open+Sans:wght@300;400&display=swap">
<style>
  :root {
    --label-tan: #b5915f;
    --leaf-cream: #e6d3b3;
    --leaf-soft: #d2b68d;
    --ink: #0d0b09;
    --serif: "Tinos", "Times New Roman", serif;
    --sans: "Open Sans", Arial, sans-serif;
  }
  * { margin: 0; padding: 0; box-sizing: border-box; }
  html, body { width: 1200px; height: 1200px; overflow: hidden; background: var(--label-tan); }
  .label {
    position: relative;
    width: 1200px;
    height: 1200px;
    background: var(--label-tan);
    color: var(--ink);
    overflow: hidden;
  }
  .botanical-art {
    position: absolute;
    inset: 0;
    width: 1200px;
    height: 1200px;
  }
  .brand-name {
    position: absolute;
    top: 98px;
    left: 0;
    width: 1208px;
    text-align: center;
    font-family: var(--serif);
    font-weight: 400;
    font-size: 56px;
    letter-spacing: 1px;
    color: var(--ink);
  }
  .tagline {
    position: absolute;
    top: 592px;
    right: 234px;
    font-family: var(--sans);
    font-weight: 400;
    font-size: 23px;
    letter-spacing: -0.2px;
    color: var(--ink);
  }
  .scent-name {
    position: absolute;
    top: 638px;
    right: 232px;
    text-align: right;
    font-family: var(--serif);
    font-weight: 700;
    font-size: 138px;
    line-height: 142px;
    letter-spacing: 1px;
    color: var(--ink);
  }
  .details {
    position: absolute;
    left: 254px;
    top: 950px;
    width: 718px;
    font-family: var(--sans);
    font-weight: 300;
    font-size: 39px;
    color: var(--ink);
  }
  .details-row {
    display: flex;
    height: 80px;
    border-top: 2px solid var(--ink);
  }
  .details-row:last-child { border-bottom: 2px solid var(--ink); }
  .details-cell {
    display: flex;
    align-items: center;
    justify-content: center;
    white-space: nowrap;
  }
  .details-cell + .details-cell { border-left: 2px solid var(--ink); }
  .row-size .details-cell:first-child { width: 240px; }
  .row-size .details-cell:last-child { flex: 1; }
  .row-origin .details-cell:first-child { width: 332px; }
  .row-origin .details-cell:last-child { flex: 1; }
</style>
</head>
<body>
  <main class="label">
    <svg class="botanical-art" viewBox="0 0 1200 1200" role="img" aria-label="Flowing cream line-art botanical leaves sweeping from the top centre across the right side and into the lower left corner">
      <defs>
        <radialGradient id="leaf-tone" cx="50%" cy="50%" r="50%">
          <stop offset="0%" stop-color="#e6d3b3" stop-opacity="0.55"/>
          <stop offset="60%" stop-color="#d2b68d" stop-opacity="0.3"/>
          <stop offset="100%" stop-color="#b5915f" stop-opacity="0"/>
        </radialGradient>
      </defs>
      <ellipse class="leaf-area leaf-top" cx="540" cy="230" rx="290" ry="250" fill="url(#leaf-tone)"/>
      <ellipse class="leaf-area leaf-stem" cx="360" cy="560" rx="110" ry="260" fill="url(#leaf-tone)"/>
      <ellipse class="leaf-area leaf-band" cx="740" cy="470" rx="330" ry="120" transform="rotate(-15 740 470)" fill="url(#leaf-tone)"/>
      <ellipse class="leaf-area leaf-right" cx="1040" cy="620" rx="220" ry="520" fill="url(#leaf-tone)"/>
      <ellipse class="leaf-area leaf-corner" cx="170" cy="940" rx="260" ry="240" fill="url(#leaf-tone)"/>
    </svg>

    <div class="brand-name">KELVANORO</div>

    <p class="tagline">made with plant based botanical</p>

    <h1 class="scent-name">JOYEAUX<br>NOEL</h1>

    <section class="details">
      <div class="details-row row-size">
        <div class="details-cell">13 oz</div>
        <div class="details-cell">Christmas Collection</div>
      </div>
      <div class="details-row row-origin">
        <div class="details-cell">kelvanoro</div>
        <div class="details-cell">made in canada</div>
      </div>
    </section>
  </main>
</body>
</html>
```